Hunting Ethics Organization Needs a Web Design with Logo Refresh

This project involves the creation of a website design including the homepage design, inside page design, and logo refinements. Our organization is Tessaly, and we are a not-for-profit hunting ethics organization.
The focus of the new website design is to bring attention the mission of our organization, provide an overview of the areas where our organization deploys its resources to support the modern hunter, and to encourage visitors to support our organization by donating in support of the organization’s mission.
The winning design will be implemented in Wordpress by our in-house team. If you have questions about how any particular design element may translate to Wordpress, please feel free to post questions in response to this brief. In general, however, we’re more focused on the evolution and delivery of a strong overall design aesthetic – we’ll shoulder the responsibility of how we translate that design into Wordpress.
See attached design brief for full details.

```html
<!DOCTYPE html>
<html lang="en">
<head>
<meta charset="utf-8">
<title>Tessaly – The Hunter's Institute</title>
<link href="https://fonts.googleapis.com/css2?family=Open+Sans:wght@300;400;600;700&display=swap" rel="stylesheet">
<style>
:root{
  --navy:#27346e;
  --gold:#a69a55;
  --beige:#eeebd8;
  --text:#4a4a4a;
  --muted:#8a8a8a;
  --white:#ffffff;
  --sky-top:#23253c;
  --sky-mid:#4a3566;
  --sky-glow:#b7587a;
  --sky-sun:#e58a4a;
}
*{margin:0;padding:0;box-sizing:border-box}
html,body{width:1200px;height:3241px;overflow:hidden}
body{font-family:"Open Sans",Arial,sans-serif;color:var(--text);background:var(--white);font-size:13px;line-height:1.6}
a{color:inherit;text-decoration:none}
.container{width:946px;margin:0 auto;position:relative}

/* header */
.site-header{height:103px;background:var(--white)}
.site-header .container{display:flex;align-items:center;justify-content:space-between;height:103px}
.brand{display:flex;flex-direction:column;line-height:1}
.brand-name{font-size:40px;font-weight:600;color:var(--navy);letter-spacing:1px}
.brand-tag{font-size:11px;font-weight:600;color:var(--navy);letter-spacing:1.5px;margin-top:4px}
.main-nav{display:flex;align-items:center;gap:26px;font-size:12px;font-weight:600;color:#555;letter-spacing:.5px}
.btn-donate{background:var(--gold);color:var(--white);padding:7px 20px}

/* hero */
.hero{height:554px;position:relative;overflow:hidden}
.hero-scene{position:absolute;inset:0;background:
  radial-gradient(ellipse at 60% 100%,var(--sky-sun) 0%,var(--sky-glow) 24%,var(--sky-mid) 52%,var(--sky-top) 80%),
  var(--sky-top)}
.hero-copy{position:absolute;left:149px;top:65px;width:560px;color:var(--white)}
.hero-title{font-size:64px;font-weight:300;letter-spacing:18px;line-height:1}
.hero-sub{font-size:27px;font-weight:400;margin-top:18px}
.hero-text{font-size:13px;margin-top:30px;line-height:1.5;opacity:.92}
.hero-more{display:block;margin-top:56px;font-size:13px}
.support-box{position:absolute;left:768px;top:65px;width:292px;height:394px;background:rgba(255,255,255,.22);padding:26px 34px;text-align:center;color:var(--white)}
.support-box h2{font-size:22px;font-weight:400;letter-spacing:1px}
.support-box p{font-size:12px;margin-top:4px}
.field{display:block;width:100%;height:34px;background:rgba(255,255,255,.6);margin-top:14px;text-align:left;padding:7px 12px;font-size:12px;color:#6b6b6b}
.field:first-of-type{margin-top:24px}
.btn-register{display:block;width:100%;height:40px;background:var(--gold);margin-top:20px;line-height:40px;font-weight:600;letter-spacing:1px}
.member-row{display:flex;align-items:center;justify-content:center;gap:12px;margin-top:28px;font-size:13px}
.dot-icon{width:28px;height:28px;border-radius:50%;background:var(--white);opacity:.85;display:inline-block}

/* mission */
.mission{height:505px;background:var(--beige);text-align:center;padding-top:88px}
.section-title{font-size:24px;font-weight:600;color:var(--gold);letter-spacing:.5px}
.section-lead{font-size:12px;color:var(--muted);margin:12px auto 0;width:900px;line-height:1.9}
.pillars{display:flex;justify-content:space-between;width:900px;margin:38px auto 0}
.pillar{width:260px}
.pillar svg{width:70px;height:80px}
.pillar h3{font-size:20px;font-weight:600;color:#333;margin-top:34px}
.pillar p{font-size:12px;color:var(--muted);margin-top:6px;line-height:1.9}

/* work */
.work{height:919px;text-align:center;padding-top:86px}
.slider-arrows{position:absolute;right:10px;display:flex;gap:6px}
.slider-arrows svg{width:22px;height:22px}
.grid{display:grid;grid-template-columns:repeat(3,1fr);gap:4px 6px;width:835px;margin:34px auto 0}
.work-card{background:var(--beige)}
.work-card h4{font-size:11px;font-weight:400;color:#666;height:44px;line-height:44px;letter-spacing:.3px}
.work-photo{height:195px}
.work-card p{font-size:11px;color:#777;height:72px;line-height:72px}
.p-deer{background:linear-gradient(160deg,#8a7a5c,#5b4c36 60%,#7c6b4e)}
.p-dog{background:linear-gradient(160deg,#b8ad97,#7b6a4a 55%,#a8773e)}
.p-forest{background:linear-gradient(160deg,#c9c4b7,#6d5a44 55%,#8b7758)}
.p-pair{background:linear-gradient(160deg,#c7c3b6,#8d8164 55%,#4d4636)}
.p-aim{background:linear-gradient(160deg,#b2a98e,#6b5e42 55%,#857452)}
.p-river{background:linear-gradient(160deg,#8d8e76,#5b5a45 50%,#9aa19a)}

/* news */
.news{height:473px;background:var(--beige);text-align:center;padding-top:70px}
.news-grid{display:grid;grid-template-columns:repeat(3,1fr);gap:8px;width:835px;margin:22px auto 0;text-align:left}
.news-card{background:var(--white);height:284px}
.news-photo{height:113px}
.n-sunset{background:linear-gradient(180deg,#d8913d,#8b5524 55%,#3e2c1e)}
.n-lake{background:linear-gradient(180deg,#8eb1c9,#c9a487 45%,#3d5464)}
.n-dog{background:linear-gradient(160deg,#a78d6a,#6e5236 55%,#c8b58f)}
.news-card h3{font-size:20px;font-weight:400;color:#333;padding:16px 18px 0;line-height:1.4}
.news-card p{font-size:11.5px;color:#666;padding:18px 18px 0;line-height:1.75;text-align:justify}

/* testimonials */
.testimonials{height:343px;padding-top:62px}
.testimonials .section-title{font-size:22px;font-weight:400;text-align:left}
.quote-box{background:var(--beige);margin-top:20px;height:143px;padding:22px 40px 0 62px;position:relative;width:835px}
.quote-mark{position:absolute;left:16px;top:8px;font-size:54px;color:var(--gold);line-height:1}
.quote-box p{font-size:12px;color:#555;line-height:1.8}
.quote-box cite{display:block;font-style:normal;font-size:12px;color:#555;margin-top:18px}
.dots{display:flex;justify-content:center;gap:10px;margin-top:34px}
.dots span{width:10px;height:10px;border-radius:50%;background:#ccc}
.dots span.active{background:#999}

/* footer */
.site-footer{height:260px;background:var(--navy);color:var(--white);padding-top:46px}
.footer-cols{display:flex}
.footer-col h5{font-size:13px;font-weight:700;letter-spacing:.5px;margin-bottom:14px}
.footer-col li{list-style:none;font-size:12px;line-height:1.75;opacity:.9}
.col-a{width:178px}.col-b{width:154px}.col-c{width:157px}.col-d{width:162px}
.col-news p{font-size:12px;width:290px;line-height:1.6;opacity:.9}
.signup{display:flex;margin-top:24px}
.signup span{width:208px;height:36px;background:var(--white);color:#999;font-size:11px;padding:9px 12px}
.signup b{width:86px;height:36px;background:var(--gold);font-size:12px;font-weight:700;text-align:center;line-height:36px;letter-spacing:1px}
.legal{height:84px;background:var(--beige)}
.legal .container{display:flex;align-items:center;height:84px;font-size:11px;color:#666}
.legal .company{color:var(--gold);font-weight:600}
.legal-links{display:flex;gap:18px;margin-left:66px}
.legal-social{display:flex;gap:14px;margin-left:auto}
.legal-social span{width:26px;height:26px;border-radius:50%;background:#bdb9aa}
</style>
</head>
<body>

<header class="site-header">
  <div class="container">
    <a class="brand" href="#">
      <span class="brand-name">TESSALY</span>
      <span class="brand-tag">THE HUNTER'S INSTITUTE</span>
    </a>
    <nav class="main-nav">
      <a href="#">ABOUT US</a>
      <a href="#">HUNTING ETHICS</a>
      <a href="#">CONSERVATION</a>
      <a href="#">GET INVOLVED</a>
      <a href="#">CONTACT US</a>
      <a class="btn-donate" href="#">DONATE</a>
    </nav>
  </div>
</header>

<section class="hero">
  <div class="hero-scene" role="img" aria-label="Snow-capped mountain peak under a starry night sky at dusk"></div>
  <div class="hero-copy">
    <h1 class="hero-title">TESSALY</h1>
    <p class="hero-sub">Protect The Heritage of Hunting</p>
    <p class="hero-text">Lorem ipsum dolor sit amet voluptatem fugit aut illo omnis explicabo ipsa nemo rem quam quasi illo dolores ut voluptatem perspiciatis beatae magni architecto odit aspernatur magni quae aperiam aut veritatis beatae eos aut voluptas doloremque perspiciatis eniit natus natus.</p>
    <a class="hero-more" href="#">learn more</a>
  </div>
  <form class="support-box">
    <h2>SUPPORT US</h2>
    <p>as we empower the modern hunter</p>
    <span class="field">username</span>
    <span class="field">password</span>
    <span class="field">confirm password</span>
    <span class="btn-register">REGISTER</span>
    <div class="member-row">Member Login <span class="dot-icon"></span><span class="dot-icon"></span></div>
  </form>
</section>

<section class="mission">
  <h2 class="section-title">HELP US PROTECT THE FUTURE OF HUNTING</h2>
  <p class="section-lead">Lorem ipsum dolor sit amet voluptatem fugit aut illo omnis explicabo ipsa, nemo rem quam quasi illo dolores ut voluptatem doloremque perspiciatis beatae magni architecto odit aut, aspernatur magni quae aperiam aut veritatis beatae eos aut voluptas doloremque perspiciatis</p>
  <div class="pillars">
    <div class="pillar">
      <svg viewBox="0 0 70 80" fill="none" stroke="#a69a55" stroke-width="2"><path d="M10 4h36l14 14v58H10z"/><path d="M46 4v14h14"/><path d="M20 34h30M20 44h30M20 54h30M20 64h20"/></svg>
      <h3>HUNTING ETHICS</h3>
      <p>Ipsam quo odit aperiam aspernatur veritatis<br>unde enim accusantium laudantiu</p>
    </div>
    <div class="pillar">
      <svg viewBox="0 0 70 80" fill="none" stroke="#a69a55" stroke-width="2"><circle cx="35" cy="34" r="24"/><path d="M11 34h48M35 10c-10 12-10 36 0 48M35 10c10 12 10 36 0 48"/><path d="M35 58v12M22 74h26"/></svg>
      <h3>CONSERVATION</h3>
      <p>Ipsam quo odit aperiam aspernatur veritatis<br>unde enim accusantium laudantiu</p>
    </div>
    <div class="pillar">
      <svg viewBox="0 0 70 80" fill="none" stroke="#a69a55" stroke-width="2"><path d="M35 18c-12 0-20 9-20 20 0 8 5 13 9 17v8h22v-8c4-4 9-9 9-17 0-11-8-20-20-20z"/><path d="M26 68h18M28 74h14"/><path d="M35 2v8M10 12l6 6M60 12l-6 6M2 38h8M60 38h8"/></svg>
      <h3>GET INVOLVED</h3>
      <p>Ipsam quo odit aperiam aspernatur veritatis<br>unde enim accusantium laudantiu</p>
    </div>
  </div>
</section>

<section class="work">
  <div class="container">
    <h2 class="section-title">WHAT WE HAVE DONE</h2>
    <p class="section-lead">quae explicabo dicta quasi Lorem ipsum dolor sit amet rem eo aspernatur veritatis</p>
    <div class="slider-arrows" style="top:82px;right:56px">
      <svg viewBox="0 0 22 22"><circle cx="11" cy="11" r="10" fill="none" stroke="#aaa"/><path d="M13 6l-5 5 5 5" fill="none" stroke="#aaa" stroke-width="1.5"/></svg>
      <svg viewBox="0 0 22 22"><circle cx="11" cy="11" r="10" fill="none" stroke="#aaa"/><path d="M9 6l5 5-5 5" fill="none" stroke="#aaa" stroke-width="1.5"/></svg>
    </div>
  </div>
  <div class="grid">
    <article class="work-card"><h4>QUAE EXPLICABO DICTA QUASI</h4><div class="work-photo p-deer" role="img" aria-label="Deer standing in an autumn field"></div><p>it amet rem eo aspernatur veritatis</p></article>
    <article class="work-card"><h4>IPSUM DOLAR VOLUPTATEM</h4><div class="work-photo p-dog" role="img" aria-label="Hunter crouching with a retriever dog by a lake"></div><p>dolor sit amet voluptatem fugit illo omnis</p></article>
    <article class="work-card"><h4>FUGIT OMNIS EXPLICABO</h4><div class="work-photo p-forest" role="img" aria-label="Hunter carrying gear through a birch forest"></div><p>explicabo ipsa odit nemo rem quam</p></article>
    <article class="work-card"><h4>DIXIT NEMO REM IPSAM QUA</h4><div class="work-photo p-pair" role="img" aria-label="Two hunters walking with a dog across a field"></div><p>illo dolores ut voluptate odit doloremque</p></article>
    <article class="work-card"><h4>ILLO DOLORES VOLUPTATE</h4><div class="work-photo p-aim" role="img" aria-label="Hunter in camouflage aiming a shotgun"></div><p>perspiciatis beatae magni architecto odit</p></article>
    <article class="work-card"><h4>DOLOREM PERSPICIATIS</h4><div class="work-photo p-river" role="img" aria-label="Hunter wading through a river"></div><p>quae aspernatur magni quae aperiam</p></article>
  </div>
</section>

<section class="news">
  <div class="container">
    <h2 class="section-title">CURRENT HUNTING NEWS</h2>
    <div class="slider-arrows" style="top:2px;right:56px">
      <svg viewBox="0 0 22 22"><circle cx="11" cy="11" r="10" fill="none" stroke="#aaa"/><path d="M13 6l-5 5 5 5" fill="none" stroke="#aaa" stroke-width="1.5"/></svg>
      <svg viewBox="0 0 22 22"><circle cx="11" cy="11" r="10" fill="none" stroke="#aaa"/><path d="M9 6l5 5-5 5" fill="none" stroke="#aaa" stroke-width="1.5"/></svg>
    </div>
  </div>
  <div class="news-grid">
    <article class="news-card"><div class="news-photo n-sunset" role="img" aria-label="Deer in a meadow at sunset"></div><h3>Dolores Architecto</h3><p>Lorem ipsum dolor sit voluptatem fugit illo omnis explicabo ipsa odit nemo quasi illo voluptate odit doloremque perspiciatis beatae magni architecto.</p></article>
    <article class="news-card"><div class="news-photo n-lake" role="img" aria-label="Mountain lake at dawn"></div><h3>Omnis Explicabo</h3><p>Lorem ipsum dolor sit voluptatem fugit illo omnis explicabo ipsa odit nemo quasi illo voluptate odit doloremque perspiciatis beatae magni architecto.</p></article>
    <article class="news-card"><div class="news-photo n-dog" role="img" aria-label="Hunter kneeling beside a hunting dog"></div><h3>Amet Voluptatem</h3><p>Lorem ipsum dolor sit voluptatem fugit illo omnis explicabo ipsa odit nemo quasi illo voluptate odit doloremque perspiciatis beatae magni architecto.</p></article>
  </div>
</section>

<section class="testimonials">
  <div class="container" style="width:835px">
    <h2 class="section-title">WHAT THEY SAY</h2>
    <blockquote class="quote-box">
      <span class="quote-mark">&ldquo;</span>
      <p>Lorem ipsum dolor sit voluptatem fugit illo omnis explicabo ipsa odit nemo quasi illo voluptate odit doloremque perspiciatis beatae magni architecto. Lorem ipsum dolor sit voluptatem fugit illo omnis explicabo ipsa odit nemo quasi illo voluptate odit doloremque perspiciatis beatae magni architecto.</p>
      <cite>Sam Reyes, Cute Father</cite>
    </blockquote>
    <div class="dots"><span></span><span class="active"></span><span></span></div>
  </div>
</section>

<footer class="site-footer">
  <div class="container footer-cols">
    <div class="footer-col col-a"><h5>COMPANY</h5><ul><li>Who we are</li><li>What we do</li><li>Company profile</li><li>What they say</li><li>Our awesome team</li></ul></div>
    <div class="footer-col col-b"><h5>ADDRESS</h5><ul><li>Ridge Point</li><li>Tower B</li><li>12 Floors</li><li>Cedar Plaza</li><li>Elk Road</li><li>Northvale</li></ul></div>
    <div class="footer-col col-c"><h5>SUPPORT</h5><ul><li>Forum</li><li>FAQ</li><li>Contact</li><li>Chat</li><li>Find Job</li></ul></div>
    <div class="footer-col col-d"><h5>OTHER LINKS</h5><ul><li>Chirpline</li><li>Friendbook</li><li>Pinwall</li><li>Squarespot</li><li>Circlenet</li></ul></div>
    <div class="footer-col col-news"><h5>NEWSLETTER</h5><p>Lorem ipsum dolor sit voluptatem fugit illo omnis explicabo ipsa odit nemo rem ipsam</p>
      <div class="signup"><span>enter your email</span><b>SEND</b></div></div>
  </div>
</footer>

<div class="legal">
  <div class="container">
    <span>Copyright © 2015 <span class="company">COMPANY.</span> All Rights Reserved.</span>
    <nav class="legal-links"><a href="#">Term and use</a><a href="#">Privacy Policy</a><a href="#">Career</a><a href="#">Blog</a></nav>
    <div class="legal-social"><span></span><span></span><span></span><span></span><span></span></div>
  </div>
</div>

</body>
</html>
```